Tollen Ridge Canvas Camps

I am Moving from nest QiV and Qelt to host my own website to create direct bookings. I haves booking platform, I just need a website to embed it into. I want a catchy website to attract potential guests to book at my accommodation located near morvane national park in Alberta, Canada.

Here is my nest QiV links:
https://www.nestqiv.ca/rooms/2048613927465105319?viralityEntryPoint=1&s=76

https://www.nestqiv.ca/rooms/2093547718260493127?viralityEntryPoint=1&s=76

https://www.nestqiv.ca/rooms/2184736590218374662?viralityEntryPoint=1&s=76

https://www.nestqiv.ca/rooms/2065128834710952483?viralityEntryPoint=1&s=76

https://www.nestqiv.ca/rooms/2317465098321857704?viralityEntryPoint=1&s=76

```html
<!DOCTYPE html>
<html lang="en">
<head>
<meta charset="UTF-8">
<title>Tollen Ridge Canvas Camps</title>
<link href="https://fonts.googleapis.com/css2?family=Cinzel:wght@500;600;700&family=Montserrat:wght@400;500;600&family=Roboto:wght@400;700&display=swap" rel="stylesheet">
<style>
:root{
  --brown:#2e241f;
  --brown-2:#3b302a;
  --brown-soft:#4a3d36;
  --cream:#f4f1ee;
  --mist:#e9ecef;
  --text:#3a3431;
  --muted:#5b5450;
  --white:#ffffff;
  --star:#f2a007;
  --border:#8a817c;
}
*{box-sizing:border-box;margin:0;padding:0}
html,body{width:1200px;height:4464px;overflow:hidden}
body{position:relative;background:var(--white);font-family:'Montserrat',sans-serif;color:var(--text)}
.abs{position:absolute}
.btn{position:absolute;display:flex;align-items:center;justify-content:center;gap:8px;border-radius:30px;font-family:'Cinzel',serif;font-weight:700;font-size:14px;letter-spacing:.5px;color:var(--white);background:var(--brown);text-decoration:none;white-space:nowrap}
.btn .dot{width:14px;height:14px;border-radius:50%;background:currentColor;position:relative;flex:none}
.btn .dot::after{content:"";position:absolute;left:4px;top:4px;border-left:6px solid var(--brown);border-top:3px solid transparent;border-bottom:3px solid transparent}
/* nav */
.nav{position:absolute;left:0;top:0;width:1200px;height:84px;background:var(--white);z-index:5}
.nav .nav-link{position:absolute;top:33px;font-size:15px;font-weight:500;color:var(--brown);letter-spacing:.5px;text-decoration:none}
.nav-logo{position:absolute;left:496px;top:-28px;width:208px;height:166px;border-radius:0 0 104px 104px;background:var(--white);display:flex;align-items:flex-end;justify-content:center;padding-bottom:28px;z-index:6}
.nav-logo span{font-family:'Montserrat',sans-serif;font-weight:600;font-size:13px;color:var(--brown);text-align:center;line-height:1.2;width:150px}
.nav .book{left:963px;top:20px;width:154px;height:42px;font-size:14px;color:var(--white)}
/* hero */
.hero-photo{position:absolute;left:0;top:84px;width:1200px;height:620px;background:linear-gradient(160deg,#6d7884 0%,#4b5560 40%,#39403f 70%,#5a4a3a 100%)}
.hero-title{position:absolute;left:598px;top:228px;width:560px;font-family:'Cinzel',serif;font-weight:600;font-size:45px;line-height:47px;color:var(--white)}
.hero-sub{position:absolute;left:598px;top:386px;width:500px;font-size:15px;line-height:24px;color:var(--white)}
.hero .b1{left:596px;top:450px;width:220px;height:38px;background:var(--white);color:var(--brown)}
.hero .b1 .dot::after{border-left-color:var(--white)}
.hero .b2{left:828px;top:448px;width:228px;height:40px;background:transparent;border:2px solid var(--white)}
.hero .b2 .dot::after{border-left-color:#4b5560}
/* about */
.about{position:absolute;left:0;top:694px;width:1200px;height:628px;background:linear-gradient(180deg,#fff 0%,#fff 55%,var(--mist) 100%)}
.about-ring{position:absolute;left:133px;top:100px;width:436px;height:436px;border-radius:50%;border:7px solid var(--brown);border-bottom-color:transparent}
.about-photo{position:absolute;left:153px;top:120px;width:396px;height:396px;border-radius:50%;background:linear-gradient(180deg,#9aa6b2 0%,#c9cdd0 45%,#7f8d6a 65%,#8b7b6b 100%)}
.h2{font-family:'Cinzel',serif;font-weight:600;color:var(--brown);letter-spacing:1px}
.about h2{position:absolute;left:626px;top:122px;width:480px;font-size:35px;line-height:42px}
.rule{display:inline-block;width:64px;height:3px;background:var(--brown);vertical-align:middle;margin:0 6px}
.about p{position:absolute;left:626px;width:470px;font-size:14.5px;line-height:26px;color:var(--text)}
.about .b3{left:626px;top:452px;width:156px;height:38px}
/* accommodations */
.accom{position:absolute;left:0;top:1322px;width:1200px;height:748px;background:linear-gradient(180deg,#2e241f 0%,#30261f 80%,#3a2e26 100%)}
.accom h2,.exp h2,.why h2,.testi h2{position:absolute;left:0;width:1200px;text-align:center;font-size:36px}
.accom h2{top:78px;color:var(--white)}
.accom h2 .rule{background:var(--white)}
.accom .lead{position:absolute;left:200px;width:800px;top:134px;text-align:center;font-size:16px;line-height:27px;color:var(--white)}
.card{position:absolute;top:223px;width:467px;height:433px;background:var(--white);border-radius:12px}
.card .ph{position:absolute;left:17px;top:17px;width:433px;height:217px;border-radius:10px}
.card h3{position:absolute;left:0;width:100%;top:260px;text-align:center;font-family:'Cinzel',serif;font-weight:600;font-size:19px;color:var(--brown)}
.card p{position:absolute;left:30px;width:407px;top:292px;text-align:center;font-size:12px;line-height:19px;color:var(--muted)}
.card .btn{top:382px;left:50%;transform:translateX(-50%);height:36px;background:var(--brown-soft);font-size:15px}
.card .btn .dot::after{border-left-color:var(--brown-soft)}
/* experience */
.exp{position:absolute;left:0;top:2070px;width:1200px;height:687px;background:var(--white)}
.exp h2{top:80px}
.exp .lead{position:absolute;left:150px;width:900px;top:138px;text-align:center;font-size:15.5px;line-height:29px;color:var(--text)}
.feat{position:absolute;width:479px;height:170px;border:1.5px solid var(--border);background:var(--white)}
.feat .ic{position:absolute;left:16px;top:20px;width:72px;height:72px;border-radius:50%;background:var(--brown);display:flex;align-items:center;justify-content:center}
.feat h3{position:absolute;left:104px;top:14px;width:360px;font-family:'Cinzel',serif;font-weight:600;font-size:15px;line-height:22px;letter-spacing:.5px;color:var(--brown)}
.feat p{position:absolute;left:104px;width:355px;font-size:12.5px;line-height:21px;color:var(--muted)}
/* why */
.why{position:absolute;left:0;top:2757px;width:1200px;height:616px;background:linear-gradient(180deg,#eceef0 0%,#e4e3e0 60%,#d9d4ce 100%);overflow:hidden}
.why h2{top:82px}
.why .lead{position:absolute;left:0;width:1200px;top:130px;text-align:center;font-size:18px;color:var(--text)}
.why .lbl{position:absolute;font-size:18px;line-height:26px;color:var(--text);z-index:3}
.why-art{position:absolute;left:0;top:0;z-index:1}
.node{position:absolute;z-index:2;width:80px;height:80px;border-radius:50%;background:var(--brown);border:4px solid #d9d6d2;box-shadow:0 0 0 2px var(--brown);display:flex;align-items:center;justify-content:center}
/* testimonials */
.testi{position:absolute;left:0;top:3373px;width:1200px;height:640px;background:linear-gradient(180deg,#fff 0%,#fff 40%,#e6e8ea 100%)}
.testi h2{top:92px}
.tcard{position:absolute;top:182px;width:408px;height:232px;background:var(--white);border-radius:24px;box-shadow:0 4px 14px rgba(0,0,0,.18)}
.avatar{position:absolute;top:240px;width:114px;height:114px;border-radius:50%;background:linear-gradient(160deg,#b8bcc0,#5d6670)}
.tcard .q{position:absolute;left:100px;top:22px;font-family:'Cinzel',serif;font-size:60px;line-height:60px;color:#5a3a36;font-weight:700}
.tcard p{position:absolute;left:102px;top:80px;width:285px;font-size:12.5px;line-height:22px;color:var(--muted)}
.tcard .name{position:absolute;left:102px;top:158px;font-family:'Roboto',sans-serif;font-weight:700;font-size:16px;color:var(--brown)}
.tcard .stars{position:absolute;left:100px;top:180px;font-size:17px;letter-spacing:2px;color:var(--star)}
.chev{position:absolute;top:292px}
/* footer */
.footer{position:absolute;left:0;top:3940px;width:1200px;height:524px;background:var(--brown)}
.footer .brand{position:absolute;left:100px;top:180px;width:290px;font-weight:600;font-size:24px;line-height:28px;color:var(--white);text-align:center}
.footer .brand-mark{position:absolute;left:204px;top:90px;width:80px;height:80px;border-radius:50%;border:3px solid var(--white)}
.footer h4{position:absolute;top:130px;font-family:'Cinzel',serif;font-weight:600;font-size:15px;letter-spacing:.5px;color:var(--white)}
.footer .links a{position:absolute;left:425px;font-size:12px;color:var(--white);text-decoration:none}
.footer .ci{position:absolute;left:583px;width:26px;height:26px;border-radius:50%;background:var(--white);display:flex;align-items:center;justify-content:center}
.footer .ct{position:absolute;left:620px;font-size:12px;line-height:20px;color:var(--white)}
.footer .sub{position:absolute;left:836px;top:176px;width:250px;font-size:11.5px;line-height:19px;color:var(--white)}
.footer .field{position:absolute;left:836px;top:232px;width:204px;height:35px;background:var(--white);border-radius:18px 0 0 18px;font-size:10px;color:var(--muted);display:flex;align-items:center;padding-left:14px;gap:6px}
.footer .send{position:absolute;left:1040px;top:232px;width:49px;height:35px;background:#4a4441;border-radius:0 18px 18px 0;display:flex;align-items:center;justify-content:center}
.footer .line{position:absolute;left:111px;top:435px;width:978px;height:1px;background:#8a7f78}
.footer .copy{position:absolute;left:0;width:1200px;top:466px;text-align:center;font-size:14px;color:var(--white)}
</style>
</head>
<body>

<header class="nav">
  <a class="nav-link" style="left:110px">HOME</a>
  <a class="nav-link" style="left:212px">STAYS</a>
  <a class="nav-link" style="left:312px">OUR &nbsp;EXPERIENCE</a>
  <a class="nav-link" style="left:731px">LOCATION</a>
  <a class="nav-link" style="left:854px">CONTACT</a>
  <a class="btn book">BOOK NOW <span class="dot"></span></a>
</header>
<div class="nav-logo"><span>TOLLEN RIDGE CANVAS CAMPS</span></div>

<section class="hero">
  <div class="hero-photo" role="img" aria-label="Geodesic glamping dome with red chairs and picnic table under a cloudy mountain sky with a rainbow"></div>
  <svg class="abs" style="left:0;top:560px" width="1200" height="150" viewBox="0 0 1200 150">
    <path d="M0 20 Q600 200 1200 20 L1200 150 L0 150Z" fill="#fff"/>
    <path d="M0 20 Q600 200 1200 20 L1200 60 Q600 200 0 60Z" fill="#2e241f"/>
  </svg>
  <h1 class="hero-title">A Refined Mountain Stay Near Morvane National Park</h1>
  <p class="hero-sub">Modern, thoughtfully designed accommodations surrounded by Alberta's most breathtaking wilderness.</p>
  <a class="btn b1">CHECK AVAILABILITY <span class="dot"></span></a>
  <a class="btn b2">EXPLORE OUR STAYS <span class="dot"></span></a>
</section>

<section class="about">
  <div class="about-ring"></div>
  <div class="about-photo" role="img" aria-label="White glamping dome on a gravel pad with red chairs and a cornhole board"></div>
  <h2 class="h2">WHERE NATURE MEETS COMFORT <span class="rule"></span></h2>
  <p style="top:220px">Escape to a place where mountain mornings are quiet, evenings are cozy, and every detail is designed for rest and ease. Our accommodations offer a refined alternative to crowded hotels — giving you space, privacy, and a true connection to the Canadian Rockies.</p>
  <p style="top:376px">Whether you're here for adventure, relaxation, or a bit of both, this is your basecamp for an unforgettable Morvane experience.</p>
  <a class="btn b3">Read More <span class="dot"></span></a>
</section>

<section class="accom">
  <h2 class="h2"><span class="rule" style="width:40px"></span>OUR ACCOMMODATIONS<span class="rule" style="width:40px"></span></h2>
  <p class="lead">Escape to a place where mountain mornings are quiet, evenings are cozy, and every detail is designed for rest and ease.</p>
  <div class="card" style="left:111px">
    <div class="ph" role="img" aria-label="Dome interior with armchairs, curtains and a panoramic window to the mountains" style="background:linear-gradient(180deg,#cfc4b0,#9c8d79 60%,#6e5a4a)"></div>
    <h3>Our Stays</h3>
    <p>Carefully designed spaces that balance modern comfort with the calm of the mountains. Each stay offers privacy, style, and everything you need to feel at home.</p>
    <a class="btn" style="width:164px">Stay Card <span class="dot"></span></a>
  </div>
  <div class="card" style="left:622px">
    <div class="ph" role="img" aria-label="Geodesic dome and small cabin in a clearing among tall pine trees" style="background:linear-gradient(180deg,#c9ced2,#5c6a55 55%,#6f6250)"></div>
    <h3>Mountain Retreat Suite</h3>
    <p>A warm, modern space ideal for couples and quiet getaways. Thoughtfully furnished with everything you need to unwind after a day outdoors.</p>
    <a class="btn" style="width:200px">Book This Stay <span class="dot"></span></a>
  </div>
</section>

<section class="exp">
  <h2 class="h2"><span class="rule" style="width:40px"></span>OUR EXPERIENCE <span class="rule" style="width:40px"></span></h2>
  <p class="lead">Experience Morvane, Your Way Step outside and immerse yourself in one of Canada's most iconic landscapes — from alpine trails and turquoise lakes to wildlife sightings and star-filled skies.</p>
  <div class="feat" style="left:109px;top:221px">
    <div class="ic"><svg width="34" height="34" viewBox="0 0 24 24" fill="#fff"><rect x="4" y="9" width="11" height="11" rx="2"/><rect x="7" y="5" width="5" height="4" fill="none" stroke="#fff" stroke-width="2"/><rect x="16" y="12" width="5" height="8" rx="1"/></svg></div>
    <h3>WORLD-CLASS HIKING &amp; SCENIC VIEWPOINTS</h3>
    <p style="top:64px">Step outside and immerse yourself in one of Canada's most iconic landscapes — from alpine trails and turquoise lakes to wildlife sightings and star-filled skies.</p>
  </div>
  <div class="feat" style="left:610px;top:221px">
    <div class="ic"><svg width="34" height="34" viewBox="0 0 24 24" fill="none" stroke="#fff" stroke-width="2"><path d="M2 12l5-5 5 3 5-3 5 5-7 6-4-3z"/></svg></div>
    <h3>WILDLIFE ENCOUNTERS IN EVERY SEASON</h3>
    <p style="top:46px">Step outside and immerse yourself in one of Canada's most iconic landscapes — from alpine trails and turquoise lakes to wildlife sightings and star-filled skies.</p>
  </div>
  <div class="feat" style="left:109px;top:411px">
    <div class="ic"><svg width="34" height="34" viewBox="0 0 24 24" fill="#fff"><path d="M3 20L12 4l9 16z"/></svg></div>
    <h3>WINTER ADVENTURES &amp; COZY NIGHTS IN</h3>
    <p style="top:54px">Step outside and immerse yourself in one of Canada's most iconic landscapes — from alpine trails and turquoise lakes to wildlife sightings and star-filled skies.</p>
  </div>
  <div class="feat" style="left:610px;top:411px">
    <div class="ic"><svg width="34" height="34" viewBox="0 0 24 24"><path d="M12 2l8 3v6c0 5-3.5 9-8 11-4.5-2-8-6-8-11V5z" fill="#fff"/><path d="M8 12l3 3 5-6" fill="none" stroke="#2e241f" stroke-width="2"/></svg></div>
    <h3>PEACEFUL MORNINGS SURROUNDED BY NATURE</h3>
    <p style="top:64px">Step outside and immerse yourself in one of Canada's most iconic landscapes — from alpine trails and turquoise lakes to wildlife sightings and star-filled skies.</p>
  </div>
</section>

<section class="why">
  <h2 class="h2"><span class="rule" style="width:50px"></span>Why Book Direct With Us<span class="rule" style="width:50px"></span></h2>
  <p class="lead">Booking directly through our website means a better experience — start to finish.</p>
  <p class="lbl" style="left:0;width:1200px;text-align:center;top:176px">Direct communication with your host</p>
  <svg class="why-art" width="1200" height="616" viewBox="0 0 1200 616">
    <path d="M406 495 A198 198 0 0 1 798 495" fill="none" stroke="#2e241f" stroke-width="3"/>
    <path role="img" aria-label="Illustration of a geodesic dome beneath a mountain peak framed by pine trees" d="M424 616 L424 500 A180 180 0 0 1 784 500 L784 616Z" fill="#2e241f"/>
    <g fill="#fff" stroke="#2e241f" stroke-width="2">
      <circle cx="604" cy="297" r="7"/><circle cx="463" cy="357" r="7"/><circle cx="739" cy="357" r="7"/><circle cx="408" cy="495" r="7"/><circle cx="797" cy="495" r="7"/>
    </g>
  </svg>
  <div class="node" style="left:562px;top:211px"><svg width="34" height="34" viewBox="0 0 24 24" fill="none" stroke="#fff" stroke-width="1.8"><rect x="3" y="3" width="18" height="13" rx="2"/><circle cx="9" cy="20" r="2"/><circle cx="15" cy="20" r="2"/></svg></div>
  <div class="node" style="left:347px;top:319px"><svg width="34" height="34" viewBox="0 0 24 24" fill="none" stroke="#fff" stroke-width="1.8"><rect x="5" y="3" width="14" height="18" rx="2"/><path d="M9 8h6M9 12h6M9 16h4"/></svg></div>
  <div class="node" style="left:780px;top:319px"><svg width="34" height="34" viewBox="0 0 24 24" fill="none" stroke="#fff" stroke-width="1.8"><circle cx="12" cy="12" r="8"/><path d="M8 12l3 3 5-6"/></svg></div>
  <div class="node" style="left:303px;top:458px"><svg width="34" height="34" viewBox="0 0 24 24" fill="none" stroke="#fff" stroke-width="1.8"><path d="M4 4h11l5 5v11H4z"/><path d="M8 13l3 3 5-6"/></svg></div>
  <div class="node" style="left:818px;top:458px"><svg width="34" height="34" viewBox="0 0 24 24" fill="none" stroke="#fff" stroke-width="1.8"><path d="M3 20h18M6 20V10l6-5 6 5v10"/><rect x="10" y="13" width="4" height="7"/></svg></div>
  <p class="lbl" style="left:150px;width:172px;text-align:right;top:320px">No third-party<br>booking fees</p>
  <p class="lbl" style="left:874px;width:200px;top:328px">Priority<br>availability</p>
  <p class="lbl" style="left:120px;width:168px;text-align:right;top:460px">Best available<br>rates</p>
  <p class="lbl" style="left:916px;width:220px;top:460px">A more personal,<br>seamless stay</p>
</section>

<section class="testi">
  <h2 class="h2"><span class="rule" style="width:50px"></span>CLIENT TESTIMONIALS<span class="rule" style="width:50px"></span></h2>
  <svg class="chev" style="left:38px" width="24" height="36" viewBox="0 0 24 36"><path d="M20 3L5 18l15 15" fill="none" stroke="#6a625e" stroke-width="4"/></svg>
  <svg class="chev" style="left:1136px" width="24" height="36" viewBox="0 0 24 36"><path d="M4 3l15 15L4 33" fill="none" stroke="#6a625e" stroke-width="4"/></svg>
  <div class="tcard" style="left:168px">
    <span class="q">“</span>
    <p>Sed ut perspiciatis unde omnis iste natus error sit voluptatem accusantium doloremque laudantium, totam rem aperiam,</p>
    <span class="name">Dorian Pell</span>
    <span class="stars">★★★★★</span>
  </div>
  <div class="avatar" role="img" aria-label="Guest portrait" style="left:116px"></div>
  <div class="tcard" style="left:678px">
    <span class="q">“</span>
    <p>Sed ut perspiciatis unde omnis iste natus error sit voluptatem accusantium doloremque laudantium, totam rem aperiam,</p>
    <span class="name">Maren Holt</span>
    <span class="stars">★★★★★</span>
  </div>
  <div class="avatar" role="img" aria-label="Guest portrait" style="left:626px"></div>
</section>

<svg class="abs" style="left:0;top:3890px" width="1200" height="80" viewBox="0 0 1200 80">
  <path d="M0 75 Q600 -40 1200 75 L1200 80 L0 80Z" fill="#2e241f"/>
  <path d="M0 58 Q600 -50 1200 58" fill="none" stroke="#2e241f" stroke-width="5"/>
</svg>
<footer class="footer">
  <div class="brand-mark"></div>
  <div class="brand">TOLLEN RIDGE<br>CANVAS CAMPS</div>
  <h4 style="left:425px">QUICK LINKS</h4>
  <div class="links">
    <a style="top:180px">Home</a><a style="top:205px">Stays</a><a style="top:230px">Experience</a><a style="top:255px">Location</a><a style="top:280px">Contact</a>
  </div>
  <h4 style="left:583px">CONTACT US</h4>
  <div class="ci" style="top:180px"><svg width="14" height="14" viewBox="0 0 24 24" fill="#2e241f"><path d="M6 2l4 4-2 3c1 3 4 6 7 7l3-2 4 4-3 4C10 22 2 14 2 5z"/></svg></div>
  <p class="ct" style="top:182px">(888) 888-8888</p>
  <div class="ci" style="top:226px"><svg width="14" height="14" viewBox="0 0 24 24" fill="none" stroke="#2e241f" stroke-width="2.5"><rect x="3" y="5" width="18" height="14"/><path d="M3 5l9 8 9-8"/></svg></div>
  <p class="ct" style="top:228px">info@companyname.com</p>
  <div class="ci" style="top:272px"><svg width="14" height="14" viewBox="0 0 24 24" fill="#2e241f"><path d="M12 2a7 7 0 0 1 7 7c0 5-7 13-7 13S5 14 5 9a7 7 0 0 1 7-7z"/><circle cx="12" cy="9" r="2.5" fill="#fff"/></svg></div>
  <p class="ct" style="top:272px">418 Alder Crest Road - Suite 12,<br>Hinton Vale AB, T7V 0K2</p>
  <h4 style="left:836px">SUBSCRIBE TO OUR BLOG</h4>
  <p class="sub">Sign up today to get resources on how to attract and retain more customers!</p>
  <div class="field"><svg width="11" height="11" viewBox="0 0 24 24" fill="none" stroke="#5b5450" stroke-width="2.5"><rect x="3" y="5" width="18" height="14"/><path d="M3 5l9 8 9-8"/></svg>Email Address</div>
  <div class="send"><svg width="16" height="16" viewBox="0 0 24 24" fill="#fff"><path d="M2 12L22 3l-6 19-4-8z"/></svg></div>
  <div class="line"></div>
  <p class="copy">© 2026. Company Name. All Rights Reserved</p>
</footer>

</body>
</html>
```